Vitamin B12 Liquid Drops Label

hi, i need a label designed for my vitamin b12 drops that i am going to be selling on shopzello. the label needs to quickly capture the attention of a buyer as he or she is scrolling through the thumbnail search results on shopzello.com my brand is called nralo. i already have an example brand logo i will be using, however, i need help designing the rest of the label. attached are some examples of labels i like for other supplements.some of these examples are pink. i do not want pink. please go for a blue/green color scheme. THE DESIGN MUST BE BOLD

Target Market(s)

adults ages 30 - 64

Font styles to use
Sans Serif

Colors
0455a3
cedeed
3176b5
85acd3
cfdeed
9bcb3b
abd037
cadf82
00a990

Requirements
Must have
• - bold design
• - somewhat gender-neutral color scheme because this will be used equally by men and women
• - B12 MUST be very prominent and visible on the label
Should not have
• - it should not be "crunchy" looking

```html
<!DOCTYPE html>
<html lang="en">
<head>
<meta charset="utf-8">
<title>Nralo Vitamin B12 Label</title>
<link rel="stylesheet" href="https://fonts.googleapis.com/css2?family=Oswald:wght@400;600&display=swap">
<style>
  :root {
    --stage-bg: #0d0d0d;
    --label-green: #9bcb3b;
    --label-blue: #0455a3;
    --title-blue: #0455a3;
    --accent-light: #cadf82;
  }
  html, body {
    margin: 0;
    padding: 0;
    width: 1200px;
    height: 800px;
    overflow: hidden;
    background: var(--stage-bg);
  }
  .stage {
    position: relative;
    width: 1200px;
    height: 800px;
    display: flex;
    align-items: center;
    justify-content: center;
  }
  .label {
    display: block;
    width: 357px;
    height: 746px;
  }
  .label-green { fill: var(--label-green); }
  .label-blue { fill: var(--label-blue); }
  .product-name {
    font-family: "Oswald", sans-serif;
    font-weight: 600;
    font-size: 62px;
    fill: var(--title-blue);
    letter-spacing: -1px;
  }
  .product-form {
    font-family: "Oswald", sans-serif;
    font-weight: 400;
    font-size: 21px;
    fill: var(--accent-light);
    letter-spacing: 4.2px;
  }
  .brand-name {
    font-family: "Oswald", sans-serif;
    font-weight: 600;
    font-size: 52px;
    fill: var(--accent-light);
  }
</style>
</head>
<body>
  <main class="stage">
    <svg class="label" viewBox="0 0 340 710" role="group" aria-label="Nralo Vitamin B12 methylcobalamin drops label">
      <rect class="label-blue" x="0" y="0" width="340" height="710"/>
      <polygon class="label-green" points="0,0 340,0 250,380 0,380"/>
      <text class="product-name" x="16" y="355" textLength="212" lengthAdjust="spacingAndGlyphs">VITAMIN B12</text>
      <text class="product-form" x="21" y="432" textLength="204" lengthAdjust="spacing">METHYLCOBAMALIN</text>
      <text class="brand-name" x="320" y="660" text-anchor="end">NRALO</text>
    </svg>
  </main>
</body>
</html>
```